Copper lark buildworks

Copper lark buildworks is a small construction company.
Who is a licenced builder, Carpenter, joiner,
working on heritage ,new build, speacial projects and sometimes furniture

Industry/Entity Type

Construction

```html
<!DOCTYPE html>
<html lang="en">
<head>
<meta charset="utf-8">
<title>Copper lark buildworks – business card</title>
<link href="https://fonts.googleapis.com/css2?family=Exo+2:wght@500&family=Lato:wght@400&display=swap" rel="stylesheet">
<style>
  :root {
    --page-bg: #e6e4e1;
    --card-white: #ffffff;
    --card-black: #0b0b0c;
    --brand-green: #8cc63f;
    --ink-dark: #1c1c1c;
    --ink-light: #ffffff;
  }
  * { box-sizing: border-box; margin: 0; padding: 0; }
  html, body {
    width: 902px;
    height: 1200px;
    overflow: hidden;
    background: var(--page-bg);
  }
  .business-card {
    position: absolute;
    left: 130px;
    top: 40px;
    width: 641px;
    height: 1120px;
    border-radius: 24px;
    overflow: hidden;
    background: var(--card-white);
    box-shadow: 0 6px 24px rgba(0,0,0,0.18);
  }
  .card-shapes {
    position: absolute;
    inset: 0;
    width: 641px;
    height: 1120px;
  }
  .brand-lockup {
    position: absolute;
    top: 118px;
    left: 0;
    width: 100%;
    display: flex;
    flex-direction: column;
    align-items: center;
    gap: 24px;
  }
  .brand-mark {
    width: 200px;
    height: 200px;
    border-radius: 50%;
    background: var(--brand-green);
  }
  .brand-name {
    font-family: "Exo 2", sans-serif;
    font-weight: 500;
    font-size: 44px;
    line-height: 1.1;
    color: var(--ink-dark);
    letter-spacing: 0.3px;
  }
  .contact-block {
    position: absolute;
    left: 0;
    width: 100%;
    text-align: center;
  }
  .person-name {
    top: 612px;
    font-family: "Exo 2", sans-serif;
    font-weight: 500;
    font-size: 36px;
    color: var(--ink-light);
    letter-spacing: 0.5px;
  }
  .person-name .surname { color: var(--brand-green); }
  .person-role {
    top: 660px;
    font-family: "Lato", sans-serif;
    font-size: 25px;
    color: var(--ink-light);
  }
  .contact-icon {
    position: absolute;
    left: 50%;
    width: 46px;
    height: 46px;
    margin-left: -23px;
  }
  .icon-phone { top: 752px; }
  .icon-mail { top: 881px; }
  .contact-phone {
    top: 808px;
    font-family: "Lato", sans-serif;
    font-size: 32px;
    color: var(--ink-light);
    letter-spacing: 0.5px;
  }
  .contact-divider {
    position: absolute;
    top: 865px;
    left: 100px;
    width: 441px;
    height: 2px;
    background: linear-gradient(90deg, transparent, var(--brand-green) 30%, var(--brand-green) 70%, transparent);
  }
  .contact-email {
    top: 932px;
    font-family: "Lato", sans-serif;
    font-size: 30px;
    color: var(--ink-light);
  }
  .contact-web {
    top: 1066px;
    font-family: "Lato", sans-serif;
    font-size: 28px;
    color: var(--ink-dark);
    letter-spacing: 2px;
  }
</style>
</head>
<body>
  <div class="business-card">
    <svg class="card-shapes" viewBox="0 0 641 1120" aria-hidden="true">
      <path d="M0 606 Q 260 470 641 508 L641 1120 L0 1120 Z" fill="var(--brand-green)"/>
      <path d="M0 626 Q 290 494 641 540 L641 1120 L0 1120 Z" fill="var(--card-black)"/>
      <path d="M118 584 Q 380 500 641 546 L641 562 Q 380 518 118 584 Z" fill="var(--card-white)"/>
      <rect x="0" y="1040" width="641" height="12" fill="var(--card-white)"/>
      <rect x="0" y="1052" width="641" height="68" fill="var(--brand-green)"/>
    </svg>

    <div class="brand-lockup">
      <span class="brand-mark"></span>
      <span class="brand-name">Copper lark buildworks</span>
    </div>

    <p class="contact-block person-name">Owen <span class="surname">Hartley</span></p>
    <p class="contact-block person-role">President</p>

    <svg class="contact-icon icon-phone" viewBox="0 0 46 46" aria-hidden="true">
      <circle cx="23" cy="23" r="20" fill="none" stroke="var(--brand-green)" stroke-width="3"/>
      <rect x="17" y="12" width="12" height="22" rx="2" fill="none" stroke="var(--brand-green)" stroke-width="2.5"/>
      <circle cx="23" cy="30" r="1.3" fill="var(--brand-green)"/>
    </svg>
    <p class="contact-block contact-phone">0431276948</p>

    <div class="contact-divider"></div>

    <svg class="contact-icon icon-mail" viewBox="0 0 46 46" aria-hidden="true">
      <circle cx="23" cy="23" r="20" fill="var(--card-black)" stroke="var(--brand-green)" stroke-width="3"/>
      <rect x="12" y="15" width="22" height="16" rx="1.5" fill="var(--brand-green)"/>
      <path d="M12.5 16 L23 24.5 L33.5 16" fill="none" stroke="var(--card-black)" stroke-width="1.8"/>
    </svg>
    <p class="contact-block contact-email">hello@copperlarkbuild.com</p>

    <p class="contact-block contact-web">www.copperlarkbuild.com</p>
  </div>
</body>
</html>
```